Flyer-Design für Ofenservice Firma
Zielgruppe
Die Firma hat als Kerngeschäft Wartung, Reinigung, Reparatur und Inbetriebnahme von Öfen und Kaminen aller Art. Der Fokus liegt dabei auf Pelletöfen. Die Firma versteht sich als zuverlässiger Dienstleister mit gutem Preisleistungsverhältnis. Zielgruppe sind hauptsächlich private Bewohner von Einfamilienhäusern in der ländlichen Gegend (Hessen)
Aufgabenstellung
Zur Bekanntmachung nach Neugründung soll ein Faltflyer gestaltet werden mit insgesamt 6 Bereichen. Die Informationen, welche auf den Flyer sollen, entnehmen Sie bitte dem Entwurf (flyer.pdf). Dieser stellt nur eine erste Idee dar und darf gerne nach Belieben verändert bzw. neu gestaltet werden. Die enthaltenen Informationen, sollten im Großen und Ganzen aber beibehalten werden. Schön wäre evtl. auch eine Hervorhebung der Preise, da wir Preisführer im Markt sind. Auch die Bilder unseres Teams sollen in den Flyer integriert sein. Auf Anfrage kann ich auch gerne weitere Kamin- und Ofenfotos zur Verfügung stellen, für welche ich die Nutzungsrechte habe. Falls Sie weitere Informationen benötigen oder Fragen haben, kommen Sie gerne auf mich zu. Die Bilder dürfen gerne etwas ausgeschnitten werden. Es geht in erster Linie darum, dass die Kunden erkennen, welche Art von Ofen sie zu Hause haben.

```html
<!DOCTYPE html>
<html lang="de">
<head>
<meta charset="utf-8">
<title>Calidor Ofenservice – Faltflyer</title>
<link rel="stylesheet" href="https://fonts.googleapis.com/css2?family=Open+Sans:wght@300;400;600;700;800&display=swap">
<style>
  :root {
    --bg: #d9d9d9;
    --paper: #ffffff;
    --paper-shade: #f2f2f2;
    --orange: #e2691f;
    --orange-light: #f08a3e;
    --slate: #3f4a54;
    --text: #5a5f64;
    --ink: #2c2f33;
  }
  * { box-sizing: border-box; margin: 0; padding: 0; }
  html, body { width: 1200px; height: 900px; overflow: hidden; }
  body {
    background: var(--bg);
    font-family: "Open Sans", Arial, sans-serif;
    display: flex;
    justify-content: center;
    align-items: center;
    gap: 0;
  }
  .panel {
    position: relative;
    width: 387px;
    height: 820px;
    background: var(--paper);
    overflow: hidden;
  }
  .panel + .panel { border-left: 1px solid #e4e4e4; }
  .panel-art { position: absolute; inset: 0; }

  /* Cover */
  .brand {
    position: absolute;
    top: 92px; left: 40px;
    display: flex; align-items: center; gap: 12px;
    font-weight: 700; font-size: 26px; letter-spacing: 1px;
    color: var(--slate);
  }
  .brand-dot { width: 16px; height: 16px; border-radius: 50%; background: var(--slate); }
  .cover-claim {
    position: absolute;
    left: 30px; bottom: 60px; right: 20px;
  }
  .cover-claim h1 {
    font-weight: 800; font-size: 27px; line-height: 1.12;
    color: var(--slate); text-transform: uppercase; letter-spacing: .3px;
  }
  .cover-claim .web {
    margin-top: 8px;
    font-weight: 700; font-size: 18px; color: var(--orange);
  }

  /* Inner panel */
  .service {
    position: absolute; top: 305px; left: 34px; right: 26px;
  }
  .service h2 { color: var(--orange); line-height: 1; }
  .service h2 .light { display: block; font-weight: 300; font-size: 34px; }
  .service h2 .bold { display: block; font-weight: 700; font-size: 36px; }
  .service-list { list-style: none; margin-top: 22px; }
  .service-list li {
    position: relative; padding-left: 30px; margin-bottom: 20px;
    font-size: 13px; line-height: 1.45; color: var(--text);
  }
  .service-list li::before {
    content: ""; position: absolute; left: 2px; top: 5px;
    width: 9px; height: 9px; border-radius: 50%; background: var(--orange);
  }
  .prices { margin-top: 10px; }
  .price-block { margin-bottom: 16px; font-size: 13px; line-height: 1.45; }
  .price-block .title { font-weight: 700; color: var(--ink); }
  .price-block .with { color: var(--orange); }
  .price-block .without { color: var(--ink); }
</style>
</head>
<body>

  <section class="panel cover">
    <svg class="panel-art" width="387" height="820" viewBox="0 0 387 820">
      <defs>
        <linearGradient id="stove" x1="0" y1="0" x2="1" y2="1">
          <stop offset="0" stop-color="#e9e6e1"/>
          <stop offset=".35" stop-color="#3b3f44"/>
          <stop offset=".6" stop-color="#d38a2b"/>
          <stop offset="1" stop-color="#2e3136"/>
        </linearGradient>
      </defs>
      <polygon points="0,262 387,150 387,162 0,274" fill="var(--orange)"/>
      <polygon role="img" aria-label="Foto eines Pelletofens mit brennendem Feuer hinter der Sichtscheibe"
               points="0,274 387,162 387,520 0,640" fill="url(#stove)"/>
      <polygon points="0,640 387,520 387,534 0,654" fill="var(--orange)"/>
      <polygon points="0,654 387,534 387,540 0,660" fill="var(--paper-shade)"/>
    </svg>
    <div class="brand"><span class="brand-dot"></span>CALIDOR Ofenservice</div>
    <div class="cover-claim">
      <h1>Kompetenter<br>Servicespezialist<br>für Öfen aller Art</h1>
      <p class="web">www.calidor-ofenservice.de</p>
    </div>
  </section>

  <section class="panel inner">
    <svg class="panel-art" width="387" height="820" viewBox="0 0 387 820">
      <defs>
        <linearGradient id="room" x1="0" y1="0" x2="1" y2="1">
          <stop offset="0" stop-color="#c9834a"/>
          <stop offset=".5" stop-color="#e6b07a"/>
          <stop offset=".8" stop-color="#f3ece4"/>
          <stop offset="1" stop-color="#b86a35"/>
        </linearGradient>
      </defs>
      <polygon role="img" aria-label="Foto eines weißen Kachelofens in einem Wohnraum mit Holzverkleidung"
               points="0,0 387,0 387,205 0,262" fill="url(#room)"/>
      <polygon points="0,262 387,205 387,219 0,276" fill="var(--orange)"/>
    </svg>
    <div class="service">
      <h2><span class="light">Grund-/</span><span class="bold">Kachelöfen</span></h2>
      <ul class="service-list">
        <li>Reinigung Schamott Verkleidung, Sichtscheibe, Zwischenboden, gesamter Feuerraum, sämtliche Rauchgaszüge, Aschebehälter</li>
        <li>Reinigung der Abgasrohre<br>(bis zu 2 m gestreckte Länge)</li>
        <li>Überprüfung der Dichtungen (Türdichtung, Türglasdichtung, Putzdeckeldichtungen)</li>
        <li>Probelauf des Gerätes</li>
      </ul>
      <div class="prices">
        <p class="price-block">
          <span class="title">Preise Kachelofen mit bis zu 4 Öffnungen</span><br>
          <span class="with">Mit Wartungsvertrag: 350 € inkl. MwSt</span><br>
          <span class="without">Ohne Wartungsvertrag: 390 € inkl. MwSt</span>
        </p>
        <p class="price-block">
          <span class="title">Preise Kachelofen mit nachgeschalteter Heizfläche</span><br>
          <span class="with">Mit Wartungsvertrag: 250 € inkl. MwSt</span><br>
          <span class="without">Ohne Wartungsvertrag: 290 € inkl. MwSt</span>
        </p>
      </div>
    </div>
  </section>

</body>
</html>
```